Web design project for exciting Australian start-up

Background
We are looking for a creative and talented web design artist to work alongside our market leading web developer.
• You will be required to create a modern and clean design theme for our website, incorporating selected rustic colour scheme elements for our exciting Australian start-up to operate within the coffee industry.
reoccurring work to be expected to flow to the successful designer.
Requirements
• c. 5 - 10 page website
• Landing page
• Log in/ out
• 404 template
• Typography is emphasised
• Please use either a) typemarrow.com, b) free web fonts, c) brindle fonts
• All design elements in vector format
• Preferably with icons for each header title(i.e. about us, how it works etc) but designer have free reign over how the site looks, so might not be applicable
• All pages to be responsive
• Down to eSlab resolution

High level visual design brief attached - additional pages to be worked from base design.

Design inspiration
• We would like to use design elements from the following sources:
http://www.zandrix.com/halcyon/ (Functionality)
Colour scheme refer to logo and complementary style guide

```html
<!DOCTYPE html>
<html lang="en">
<head>
<meta charset="utf-8">
<title>Brewline — Marketplace</title>
<link rel="stylesheet" href="https://fonts.googleapis.com/css2?family=Mulish:wght@400;600;700;800&family=Roboto+Slab:wght@400;500&display=swap">
<style>
  :root{
    --red:#e63236;
    --orange:#f99d2a;
    --ink:#222;
    --text:#444;
    --muted:#888;
    --line:#e2e2e2;
    --card:#f6f6f6;
    --footer:#e8e8e8;
    --base:#4d4d4d;
    --white:#fff;
  }
  *{box-sizing:border-box;margin:0;padding:0}
  html,body{width:1200px;height:989px;overflow:hidden;background:var(--white)}
  body{font-family:"Mulish",sans-serif;color:var(--text);font-size:13px;position:relative}
  .wrap{position:absolute;left:161px;width:878px}

  /* header */
  .site-header{position:absolute;top:0;left:0;width:1200px;height:107px;border-bottom:1px solid var(--line);box-shadow:0 2px 4px rgba(0,0,0,.04)}
  .brand{position:absolute;left:161px;top:36px;display:flex;align-items:center;gap:10px;font-weight:800;font-size:25px;letter-spacing:2px;color:var(--ink)}
  .brand-dot{width:30px;height:30px;border-radius:50%;background:var(--orange)}
  .main-nav{position:absolute;left:423px;top:0;height:107px;display:flex}
  .main-nav a{display:flex;flex-direction:column;align-items:center;justify-content:center;gap:8px;height:107px;border-left:1px solid var(--line);color:#333;text-decoration:none;font-size:11.5px;text-transform:uppercase}
  .main-nav a:last-child{border-right:1px solid var(--line)}
  .nav-about{width:94px}.nav-how{width:135px}.nav-faq{width:66px}
  .account{position:absolute;top:38px;left:750px;display:flex;gap:9px}
  .btn{display:inline-flex;align-items:center;justify-content:center;color:var(--white);border-radius:2px;font-size:13.5px;text-decoration:none}
  .btn-red{background:var(--red)}.btn-orange{background:var(--orange)}
  .account .btn{height:31px}

  /* marketplace */
  .section-title{font-weight:800;font-size:17px;color:var(--ink);text-transform:uppercase}
  .market-title{top:141px}
  .filters{top:169px;height:36px;display:flex}
  .filters .btn{height:36px;font-size:14px;position:absolute;top:0}
  .search-bar{top:222px;height:34px;display:flex;align-items:center}
  .clear{position:absolute;left:0;width:33px;height:33px;border-radius:50%;background:var(--red);color:var(--white);display:flex;align-items:center;justify-content:center;font-weight:800;font-size:14px}
  .search-label{position:absolute;font-size:13px;color:#333}
  .select{position:absolute;left:632px;width:139px;height:32px;border:1px solid #ddd;display:flex;align-items:center;padding-left:13px;color:var(--muted)}
  .select .caret{position:absolute;right:11px;top:13px}
  .view-btn{position:absolute;left:823px;width:54px;height:32px;border:1px solid #ddd;display:flex;align-items:center;padding-left:9px;gap:12px}
  .divider{top:272px;border-top:1px solid var(--line)}
  .results-title{top:313px}

  /* result cards */
  .result{height:135px;border:1px solid #ddd;background:var(--card)}
  .result-photo{position:absolute;left:8px;top:7px;width:160px;height:119px;border-radius:2px}
  .photo-a{background:linear-gradient(135deg,#eee4d8,#c9a78b 55%,#e7dccf)}
  .photo-b{background:linear-gradient(135deg,#b9b2a8,#8c2b26 40%,#e9e1d5 60%,#4a5a3a)}
  .bean-info{position:absolute;left:186px;top:22px;line-height:22.5px}
  .bean-name{color:var(--red);font-weight:700;font-size:13px}
  .spec{display:flex}.spec span:first-child{width:125px}.spec span:nth-child(2){width:12px}
  .reviews{position:absolute;right:30px;top:18px;width:246px;height:100px}
  .reviews h3{position:absolute;right:0;top:4px;font-size:15.5px;font-weight:700;color:var(--ink)}
  .bubble{position:absolute;left:0;top:3px}
  .stars{position:absolute;left:0;top:30px;display:flex;gap:3px}
  .rating-note{position:absolute;right:0;top:27px;text-align:right;line-height:16px}
  .tools{position:absolute;left:0;top:84px;display:flex;gap:11px}
  .offers{position:absolute;right:0;top:85px}

  /* footer */
  .site-footer{position:absolute;left:0;top:684px;width:1200px;height:236px;background:var(--footer)}
  .foot-col{position:absolute;top:52px}
  .foot-col h4{font-family:"Roboto Slab",serif;font-weight:500;font-size:17.5px;letter-spacing:.5px;color:var(--ink);text-transform:uppercase;margin-bottom:16px}
  .foot-col a{display:flex;align-items:center;gap:16px;height:31px;color:var(--text);text-decoration:none;font-size:13.5px}
  .foot-col .social-mark{width:10px;height:10px;background:#555;border-radius:1px}
  .base{position:absolute;left:0;top:920px;width:1200px;height:69px;background:var(--base)}
  .base .rule{position:absolute;left:161px;width:878px;top:5px;border-top:1px solid #606060}
  .base p{position:absolute;width:1200px;top:27px;text-align:center;color:var(--white);font-size:13.5px}
</style>
</head>
<body>

<header class="site-header">
  <div class="brand"><span>BREWLINE</span><span class="brand-dot"></span></div>
  <nav class="main-nav">
    <a class="nav-about" href="#">
      <svg width="18" height="18" viewBox="0 0 18 18" fill="none" stroke="#f99d2a" stroke-width="1.3"><path d="M2 9 9 2l7 7M4 7.5V16h4v-4h2v4h4V7.5"/></svg>
      About us</a>
    <a class="nav-how" href="#">
      <svg width="20" height="18" viewBox="0 0 20 18" fill="none" stroke="#888" stroke-width="1.2"><circle cx="7" cy="7" r="3"/><path d="M2 17c0-4 2.5-6 5-6s5 2 5 6M11 2h7v6h-4l-2 2V8"/></svg>
      How it works</a>
    <a class="nav-faq" href="#">
      <svg width="16" height="18" viewBox="0 0 16 18" fill="none" stroke="#888" stroke-width="1.2"><rect x="2" y="4" width="4" height="13"/><rect x="9" y="1" width="5" height="16"/><path d="M3.5 7h1M10.5 5h2"/></svg>
      FAQ</a>
  </nav>
  <div class="account">
    <a class="btn btn-red" style="width:118px" href="#">My Account</a>
    <a class="btn btn-orange" style="width:76px" href="#">Login</a>
    <a class="btn btn-red" style="width:76px" href="#">Sign up</a>
  </div>
</header>

<h1 class="wrap section-title market-title">Marketplace</h1>

<div class="wrap filters">
  <a class="btn btn-orange" style="left:0;width:122px" href="#">Tender format</a>
  <a class="btn btn-red" style="left:131px;width:96px" href="#">All</a>
  <a class="btn btn-orange" style="left:237px;width:96px" href="#">One-off</a>
  <a class="btn btn-orange" style="left:342px;width:96px" href="#">Recurring</a>
  <a class="btn btn-orange" style="left:675px;width:97px" href="#">Quantity (kg)</a>
  <a class="btn btn-red" style="left:781px;width:97px" href="#">35 kg/week</a>
</div>

<div class="wrap search-bar">
  <span class="clear">x</span>
  <span class="search-label" style="left:42px">Results for Café Morrow</span>
  <svg style="position:absolute;left:193px;top:4px" width="25" height="24" viewBox="0 0 24 23"><path fill="#f99d2a" d="M12 0l3.6 7.6 8.4 1-6.2 5.8 1.6 8.3L12 18.6l-7.4 4.1 1.6-8.3L0 8.6l8.4-1z"/></svg>
  <span class="search-label" style="left:223px">Save search</span>
  <span class="search-label" style="left:598px">Sort</span>
  <div class="select">Highest rated
    <svg class="caret" width="9" height="5" viewBox="0 0 9 5"><path fill="#e63236" d="M0 0h9L4.5 5z"/></svg></div>
  <span class="search-label" style="left:785px">View</span>
  <div class="view-btn">
    <svg width="18" height="16" viewBox="0 0 18 16" fill="#f99d2a"><rect width="8" height="7"/><rect x="10" width="8" height="7"/><rect y="9" width="8" height="7"/><rect x="10" y="9" width="8" height="7"/></svg>
    <svg width="9" height="5" viewBox="0 0 9 5"><path fill="#e63236" d="M0 0h9L4.5 5z"/></svg>
  </div>
</div>

<div class="wrap divider"></div>

<h2 class="wrap section-title results-title">Results</h2>

<article class="wrap result" style="top:347px">
  <div class="result-photo photo-a" role="img" aria-label="Photo of a latte with heart foam art on a white saucer"></div>
  <div class="bean-info">
    <div class="bean-name">Coffee bean XX</div>
    <div>Blend description:</div>
    <div class="spec"><span>Origin</span><span>:</span><span>[xx]</span></div>
    <div class="spec"><span>Grind availability</span><span>:</span><span>[xx]</span></div>
  </div>
  <div class="reviews">
    <svg class="bubble" width="32" height="24" viewBox="0 0 32 24"><path fill="#f99d2a" d="M16 0C7 0 0 4.5 0 10s5 8.6 11 9.7L9 24l7-4c9 0 16-4.5 16-10S25 0 16 0z"/></svg>
    <h3>Reviews for this bean</h3>
    <div class="stars">
      <svg width="15" height="14" viewBox="0 0 24 23"><path fill="#f99d2a" d="M12 0l3.6 7.6 8.4 1-6.2 5.8 1.6 8.3L12 18.6l-7.4 4.1 1.6-8.3L0 8.6l8.4-1z"/></svg>
      <svg width="15" height="14" viewBox="0 0 24 23"><path fill="#f99d2a" d="M12 0l3.6 7.6 8.4 1-6.2 5.8 1.6 8.3L12 18.6l-7.4 4.1 1.6-8.3L0 8.6l8.4-1z"/></svg>
      <svg width="15" height="14" viewBox="0 0 24 23"><path fill="#f99d2a" d="M12 0l3.6 7.6 8.4 1-6.2 5.8 1.6 8.3L12 18.6l-7.4 4.1 1.6-8.3L0 8.6l8.4-1z"/></svg>
      <svg width="15" height="14" viewBox="0 0 24 23"><path fill="#ccc" d="M12 0l3.6 7.6 8.4 1-6.2 5.8 1.6 8.3L12 18.6l-7.4 4.1 1.6-8.3L0 8.6l8.4-1z"/></svg>
      <svg width="15" height="14" viewBox="0 0 24 23"><path fill="#ccc" d="M12 0l3.6 7.6 8.4 1-6.2 5.8 1.6 8.3L12 18.6l-7.4 4.1 1.6-8.3L0 8.6l8.4-1z"/></svg>
    </div>
    <div class="rating-note">Wholesaler's overall<br>customer rating</div>
    <div class="tools">
      <svg width="13" height="13" viewBox="0 0 13 13"><rect width="13" height="13" rx="2" fill="#999"/><path d="M3 10l1-3 4-4 2 2-4 4z" fill="#fff"/></svg>
      <svg width="15" height="13" viewBox="0 0 15 13"><rect y="3" width="15" height="10" rx="4" fill="#999"/><circle cx="5" cy="8" r="1.6" fill="#fff"/><circle cx="10" cy="8" r="1.6" fill="#fff"/></svg>
      <svg width="13" height="14" viewBox="0 0 13 14"><path fill="#999" d="M6.5 0C4 0 3 2 3 4v4L1 11h11L10 8V4c0-2-1-4-3.5-4zM5 12h3a1.5 1.5 0 0 1-3 0z"/></svg>
      <svg width="14" height="14" viewBox="0 0 14 14"><circle cx="7" cy="7" r="7" fill="#999"/><path d="M3 4c2 0 2 2 4 2s1 3-1 3M9 2c1 2 3 2 3 5" stroke="#fff" fill="none"/></svg>
    </div>
    <div class="offers">Other offerings</div>
  </div>
</article>

<article class="wrap result" style="top:503px">
  <div class="result-photo photo-b" role="img" aria-label="Photo of a festive patterned mug of coffee among pine branches and berries"></div>
  <div class="bean-info">
    <div class="bean-name">Coffee bean XX</div>
    <div>Blend description:</div>
    <div class="spec"><span>Origin</span><span>:</span><span>[xx]</span></div>
    <div class="spec"><span>Grind availability</span><span>:</span><span>[xx]</span></div>
  </div>
  <div class="reviews">
    <svg class="bubble" width="32" height="24" viewBox="0 0 32 24"><path fill="#f99d2a" d="M16 0C7 0 0 4.5 0 10s5 8.6 11 9.7L9 24l7-4c9 0 16-4.5 16-10S25 0 16 0z"/></svg>
    <h3>Reviews for this bean</h3>
    <div class="stars">
      <svg width="15" height="14" viewBox="0 0 24 23"><path fill="#f99d2a" d="M12 0l3.6 7.6 8.4 1-6.2 5.8 1.6 8.3L12 18.6l-7.4 4.1 1.6-8.3L0 8.6l8.4-1z"/></svg>
      <svg width="15" height="14" viewBox="0 0 24 23"><path fill="#f99d2a" d="M12 0l3.6 7.6 8.4 1-6.2 5.8 1.6 8.3L12 18.6l-7.4 4.1 1.6-8.3L0 8.6l8.4-1z"/></svg>
      <svg width="15" height="14" viewBox="0 0 24 23"><path fill="#f99d2a" d="M12 0l3.6 7.6 8.4 1-6.2 5.8 1.6 8.3L12 18.6l-7.4 4.1 1.6-8.3L0 8.6l8.4-1z"/></svg>
      <svg width="15" height="14" viewBox="0 0 24 23"><path fill="#ccc" d="M12 0l3.6 7.6 8.4 1-6.2 5.8 1.6 8.3L12 18.6l-7.4 4.1 1.6-8.3L0 8.6l8.4-1z"/></svg>
      <svg width="15" height="14" viewBox="0 0 24 23"><path fill="#ccc" d="M12 0l3.6 7.6 8.4 1-6.2 5.8 1.6 8.3L12 18.6l-7.4 4.1 1.6-8.3L0 8.6l8.4-1z"/></svg>
    </div>
    <div class="rating-note">Wholesaler's overall<br>customer rating</div>
    <div class="tools">
      <svg width="13" height="13" viewBox="0 0 13 13"><rect width="13" height="13" rx="2" fill="#999"/><path d="M3 10l1-3 4-4 2 2-4 4z" fill="#fff"/></svg>
      <svg width="15" height="13" viewBox="0 0 15 13"><rect y="3" width="15" height="10" rx="4" fill="#999"/><circle cx="5" cy="8" r="1.6" fill="#fff"/><circle cx="10" cy="8" r="1.6" fill="#fff"/></svg>
      <svg width="13" height="14" viewBox="0 0 13 14"><path fill="#999" d="M6.5 0C4 0 3 2 3 4v4L1 11h11L10 8V4c0-2-1-4-3.5-4zM5 12h3a1.5 1.5 0 0 1-3 0z"/></svg>
      <svg width="14" height="14" viewBox="0 0 14 14"><circle cx="7" cy="7" r="7" fill="#999"/><path d="M3 4c2 0 2 2 4 2s1 3-1 3M9 2c1 2 3 2 3 5" stroke="#fff" fill="none"/></svg>
    </div>
    <div class="offers">Other offerings</div>
  </div>
</article>

<footer class="site-footer">
  <div class="foot-col" style="left:295px">
    <h4>Helpful info</h4>
    <a href="#">About Us</a>
    <a href="#">Media Enquiries</a>
    <a href="#">Terms &amp; Conditions</a>
    <a href="#">Privacy Policy</a>
  </div>
  <div class="foot-col" style="left:541px">
    <h4>Who we are</h4>
    <a href="#" style="padding-left:8px">How it works</a>
    <a href="#" style="padding-left:8px">FAQ</a>
    <a href="#" style="padding-left:8px">Contact us</a>
  </div>
  <div class="foot-col" style="left:797px">
    <h4>Join us on</h4>
    <a href="#" style="padding-left:3px">Socialbook <span class="social-mark"></span></a>
    <a href="#" style="padding-left:3px">Chirper <span class="social-mark"></span></a>
    <a href="#" style="padding-left:3px">Linkfolio <span class="social-mark"></span></a>
    <a href="#" style="padding-left:3px">ViewTube <span class="social-mark"></span></a>
  </div>
</footer>

<div class="base">
  <div class="rule"></div>
  <p>Copyright © 2014 Brewline</p>
</div>

</body>
</html>
```